DL size flyer design for renovations and extensions construction company

We are looking for a flyer design for a construction company specialising in renovations, extensions, and minor building works. The aim is for anyone needing any home construction works to pick up the phone and call us. The flyers will be delivered primarily to letterboxes of homes. We want the flyers to stick out from all the other things people get in the mail by any means possible.

Target Market(s)

The audience we target is residential home owners and are looking to deliver these letters to home letterboxes.

Industry/Entity Type

Residential Construction

Font styles to use
Sans Serif

Colors
000000
ffffff

Requirements
Must have
• 1 - Places for 4 photos with descriptions reading: (1) Bathroom Renovations (4) Kitchen Renovations (3) Home Extensions (4) Outdoor works and landscaping. This may be on the reverse side of the DL flyer.
• 2 - Fonts to be used are (1) Brandon Grotesque (All caps) for main heading, (2) Montserrat SemiBold (All caps) for Headings, (3) Lato for text.
• 3 - Copy of the finished document in PDF and indesign formats.
• 4 - Placeholders for copy (look at the brindlecove.com website for now)
Nice to have
• A modern looking design.
Should not have
• Not all photos attached are necessarily required. Up to you to use your creativity to decide on the best combination.

```html
<!DOCTYPE html>
<html lang="en">
<head>
<meta charset="utf-8">
<title>Brindle Cove – DL Flyer</title>
<link href="https://fonts.googleapis.com/css2?family=Lato:wght@400;700&family=Montserrat:wght@600;700;800&display=swap" rel="stylesheet">
<style>
  :root{
    --green:#12944a;
    --black:#111111;
    --white:#ffffff;
    --stage:#e4e4e4;
    --band:#f2f2f2;
    --frame:#b9a48c;
    --text:#222222;
  }
  *{box-sizing:border-box;margin:0;padding:0}
  html,body{width:1200px;height:943px;overflow:hidden;background:var(--stage)}
  body{position:relative;font-family:"Lato",sans-serif;color:var(--text)}
  .flyer{position:absolute;top:43px;width:435px;height:872px;background:var(--white);overflow:hidden}
  .flyer--front{left:126px}
  .flyer--back{left:676px}
  .abs{position:absolute}

  /* front */
  .headline{left:38px;top:32px;font-family:"Montserrat",sans-serif;font-weight:800;font-size:22px;line-height:34px;text-transform:uppercase;color:var(--black);letter-spacing:-0.2px;white-space:nowrap}
  .headline .accent{color:var(--green)}
  .service-icon{width:46px;height:46px;top:127px}
  .service-label{top:189px;width:120px;text-align:center;font-family:"Montserrat",sans-serif;font-weight:600;font-size:15px;letter-spacing:.5px;color:var(--black)}
  .green-rule{left:0;top:233px;width:100%;height:5px;background:var(--green)}
  .hero-photo{left:0;top:238px;width:100%;height:473px;background:linear-gradient(160deg,#f1efec 0%,#d9d3cb 45%,#9aa4b5 70%,#c8c2b8 100%)}
  .black-rule{left:0;width:100%;height:6px;background:var(--black)}
  .brand{width:100%;text-align:center;font-family:"Montserrat",sans-serif;font-weight:800;color:var(--black);text-transform:uppercase;letter-spacing:1px}
  .web{width:100%;display:flex;justify-content:center;align-items:center;gap:10px;font-family:"Lato",sans-serif;font-size:16px;color:var(--black)}
  .web b{color:var(--green);font-weight:700}
  .web::before,.web::after{content:"";width:66px;height:2px;background:var(--green)}

  /* back */
  .band{left:0;width:100%;background:linear-gradient(90deg,var(--band),#fafafa 60%,var(--band))}
  .service-photo{width:143px;height:96px;border:3px solid var(--frame);box-shadow:inset 0 0 0 3px var(--white)}
  .service-photo--bath{background:linear-gradient(135deg,#eeeeec,#b9b4ac 60%,#7d7a74)}
  .service-photo--kitchen{background:linear-gradient(135deg,#f4f3f1,#d6d1ca 55%,#a59f96)}
  .service-photo--extension{background:linear-gradient(135deg,#e9e4dc,#b88a5a 55%,#4f5b46)}
  .service-title{font-family:"Montserrat",sans-serif;font-weight:700;font-size:15px;line-height:19px;color:var(--green);text-transform:uppercase}
  .service-text{font-size:12.5px;line-height:15.3px;color:var(--text);margin-top:4px}
  .quote{width:100%;text-align:center;font-family:"Montserrat",sans-serif;font-weight:700;font-size:24px;text-transform:uppercase;color:var(--black)}
  .quote .tag{background:var(--green);color:var(--white);padding:0 4px;border-radius:4px}
  .phone{width:100%;text-align:center;font-family:"Montserrat",sans-serif;font-weight:700;font-size:36px;color:var(--black);letter-spacing:.5px}
  .contact{width:100%;display:flex;justify-content:center;align-items:center;gap:12px;font-size:13px;color:var(--text)}
  .contact span{display:flex;align-items:center;gap:6px}
  .contact .divider{width:2px;height:24px;background:var(--green)}
</style>
</head>
<body>

<section class="flyer flyer--front">
  <h1 class="headline abs">Looking to make your<br><span class="accent">home bigger or better?</span></h1>

  <svg class="service-icon abs" style="left:65px" viewBox="0 0 46 46" aria-hidden="true">
    <circle cx="23" cy="23" r="23" fill="var(--green)"/>
    <path d="M13 33 L31 15 M15 15 L33 33" stroke="#fff" stroke-width="4" stroke-linecap="round"/>
    <rect x="11" y="11" width="10" height="6" fill="#fff" transform="rotate(45 16 14)"/>
  </svg>
  <svg class="service-icon abs" style="left:187px" viewBox="0 0 46 46" aria-hidden="true">
    <circle cx="23" cy="23" r="23" fill="var(--white)"/>
    <circle cx="23" cy="23" r="17" fill="var(--green)"/>
    <path d="M6 18 A18 18 0 0 1 36 9 M40 28 A18 18 0 0 1 10 37" stroke="var(--green)" stroke-width="3" fill="none"/>
    <rect x="17" y="13" width="12" height="20" fill="#fff"/>
    <path d="M19 16h3M24 16h3M19 20h3M24 20h3M19 24h3M24 24h3" stroke="var(--green)" stroke-width="2"/>
  </svg>
  <svg class="service-icon abs" style="left:318px" viewBox="0 0 46 46" aria-hidden="true">
    <circle cx="23" cy="23" r="23" fill="var(--green)"/>
    <path d="M12 12l7 7M34 12l-7 7M12 34l7-7M34 34l-7-7M12 12h6M12 12v6M34 12h-6M34 12v6M12 34h6M12 34v-6M34 34h-6M34 34v-6" stroke="#fff" stroke-width="3" stroke-linecap="round"/>
  </svg>
  <div class="service-label abs" style="left:28px">BUILD</div>
  <div class="service-label abs" style="left:150px">RENOVATE</div>
  <div class="service-label abs" style="left:281px">EXTEND</div>

  <div class="green-rule abs"></div>
  <div class="hero-photo abs" role="img" aria-label="Family sharing breakfast in a bright renovated kitchen"></div>
  <div class="black-rule abs" style="top:711px"></div>

  <div class="brand abs" style="top:753px;font-size:34px">Brindle Cove</div>
  <div class="web abs" style="top:828px"><span>www.<b>brindlecove</b>.com</span></div>
</section>

<section class="flyer flyer--back">
  <div class="brand abs" style="top:54px;font-size:28px">Brindle Cove</div>

  <div class="service-photo service-photo--bath abs" style="left:28px;top:129px" role="img" aria-label="Modern bathroom with walk-in shower and freestanding bath"></div>
  <div class="abs" style="left:195px;top:141px;width:225px">
    <h2 class="service-title">Bathroom Renovations</h2>
    <p class="service-text">We create custom bathroom renovations of various shapes and sizes to suit a variety of family needs.</p>
  </div>

  <div class="band abs" style="top:238px;height:122px"></div>
  <div class="abs" style="left:26px;top:264px;width:230px">
    <h2 class="service-title">Kitchen Renovations</h2>
    <p class="service-text">Today's kitchens go further than places to just make a meal - they are the open-plan hub for the modern home.</p>
  </div>
  <div class="service-photo service-photo--kitchen abs" style="left:267px;top:252px" role="img" aria-label="Bright open kitchen with white cabinetry"></div>

  <div class="service-photo service-photo--extension abs" style="left:28px;top:378px" role="img" aria-label="Open-plan dining extension with timber floor"></div>
  <div class="abs" style="left:195px;top:377px;width:225px">
    <h2 class="service-title">Home Extensions</h2>
    <p class="service-text">Brindle Cove are licenced builders experienced at delivering structural alterations or home extensions, and we are always guided by our qualified engineers.</p>
  </div>

  <div class="band abs" style="top:491px;height:123px"></div>
  <div class="abs" style="left:26px;top:503px;width:230px">
    <h2 class="service-title">Outdoor works and<br>landscaping</h2>
    <p class="service-text">Home living spans across both internal and external environments and a complete home needs to consider integration into the surrounding land.</p>
  </div>
  <div class="service-photo service-photo--bath abs" style="left:267px;top:504px" role="img" aria-label="Finished renovation interior with glass screen"></div>

  <div class="black-rule abs" style="top:661px"></div>

  <div class="quote abs" style="top:706px">Request<span class="tag">A quote</span></div>
  <div class="phone abs" style="top:739px">0412 555 018</div>
  <div class="contact abs" style="top:794px">
    <span><svg width="12" height="9" viewBox="0 0 12 9" aria-hidden="true"><rect width="12" height="9" fill="var(--green)"/><path d="M0 0l6 5 6-5" stroke="#fff" fill="none"/></svg>info@brindlecove.com</span>
    <i class="divider"></i>
    <span><svg width="10" height="13" viewBox="0 0 10 13" aria-hidden="true"><path d="M5 13C5 13 0 7 0 5a5 5 0 0 1 10 0c0 2-5 8-5 8z" fill="var(--green)"/><circle cx="5" cy="5" r="2" fill="#fff"/></svg>Sydney, NSW.</span>
  </div>
  <div class="web abs" style="top:834px"><span>www.<b>brindlecove</b>.com</span></div>
</section>

</body>
</html>
```